Social Media Graphics - Oakline Push REVISED

Create 6-7 individual social media graphics (square size) to encourage folks to join our online course called:

The Harvest Ledger Circle
How to Launch a Multi-Million Business From Scratch
Sign Up Today!

IMPORTANT: Make the largest and most prominent text on the graphic be: How to Launch a Multi-Million Business From Scratch

For the color scheme of the graphics, let's try a blue color palette; make sure the graphics appeal to both men and women

Make sure each graphic contains 1 of the 3 pics attached (crop pic as needed); and make sure one of the graphics is all TEXT only.

Target Market(s)

men and women looking to start a business

Industry/Entity Type

Entrepreneurship

Colors
0054AA
0677BA
7BADD7
CADEEF
E8F1F8

Requirements
Must have
• All the text and use the 3 pics provided; one graphic can be all text; Simple, modern design that's easy to read

```html
<!DOCTYPE html>
<html lang="en">
<head>
<meta charset="utf-8">
<title>The Harvest Ledger Circle – Social Graphics</title>
<link href="https://fonts.googleapis.com/css2?family=Bebas+Neue&family=Oswald:wght@500;600&display=swap" rel="stylesheet">
<style>
  :root {
    --navy: #0054AA;
    --mid: #0677BA;
    --sky: #7BADD7;
    --mist: #CADEEF;
    --ice: #E8F1F8;
    --board: #A8CCE3;
    --white: #FFFFFF;
  }
  * { margin: 0; padding: 0; box-sizing: border-box; }
  html, body { width: 1200px; height: 902px; overflow: hidden; }
  body { background: var(--board); position: relative; font-family: "Bebas Neue", "Oswald", sans-serif; }

  .tile { position: absolute; width: 310px; height: 310px; overflow: hidden;
          background: linear-gradient(160deg, var(--navy) 0%, var(--mid) 55%, var(--navy) 100%); color: var(--white); }
  .tile--1 { left: 118px; top: 143px; }
  .tile--2 { left: 461px; top: 143px; }
  .tile--3 { left: 803px; top: 143px; }
  .tile--4 { left: 118px; top: 483px; }
  .tile--5 { left: 461px; top: 483px; }
  .tile--6 { left: 803px; top: 483px; }

  .course-name { position: absolute; font-family: "Oswald", sans-serif; font-weight: 600; font-style: italic;
                 text-transform: uppercase; font-size: 23px; letter-spacing: -0.5px; line-height: 1; white-space: nowrap;
                 text-shadow: 1px 2px 3px rgba(0,0,0,0.35); }
  .course-name--dark { color: var(--navy); text-shadow: none; }

  .headline { position: absolute; text-transform: uppercase; line-height: 0.98; }
  .headline--lead { left: 15px; top: 63px; font-size: 50px; line-height: 0.99; }
  .headline--centered { left: 0; width: 310px; text-align: center; font-size: 36px; line-height: 1.1; }

  .badge { position: absolute; width: 92px; height: 84px; filter: drop-shadow(0 0 4px rgba(255,255,255,0.7)); }
  .badge svg { position: absolute; inset: 0; }
  .badge span { position: absolute; left: 0; top: 9px; width: 92px; text-align: center; font-size: 29px; line-height: 0.88;
                color: var(--white); -webkit-text-stroke: 1px var(--mid); }
  .badge--sm { transform: scale(0.72); transform-origin: 0 0; }

  .photo { position: absolute; background: linear-gradient(180deg, var(--sky), var(--navy)); border-radius: 6px; opacity: 0.9; }
  .band { position: absolute; left: 0; width: 310px; }
</style>
</head>
<body>

<!-- text only -->
<section class="tile tile--1">
  <h2 class="course-name" style="left:14px; top:16px;">The Harvest Ledger Circle</h2>
  <h1 class="headline headline--lead">How to launch<br>a multi-million<br>business from<br>scratch</h1>
  <div class="badge" style="left:190px; top:222px;">
    <svg viewBox="0 0 92 84" width="92" height="84"><path d="M10 4 H84 V66 H48 L34 80 V66 H10 Z" fill="none" stroke="#fff" stroke-width="2"/></svg>
    <span>Sign up<br>today!</span>
  </div>
</section>

<!-- diagonal split -->
<section class="tile tile--2">
  <svg class="band" style="top:0; height:310px;" viewBox="0 0 310 310" width="310" height="310">
    <path d="M0 310 L0 290 L40 240 L120 170 L200 100 L310 0 L310 310 Z" fill="#0054AA"/>
  </svg>
  <h2 class="course-name" style="left:14px; top:17px;">The Harvest Ledger Circle</h2>
  <div class="photo" role="img" aria-label="Photo of the two course hosts standing with arms crossed" style="left:128px; top:56px; width:160px; height:128px;"></div>
  <div class="badge" style="left:20px; top:72px;">
    <svg viewBox="0 0 92 84" width="92" height="84"><path d="M10 4 H84 V66 H48 L34 80 V66 H10 Z" fill="none" stroke="#fff" stroke-width="2"/></svg>
    <span>Sign up<br>today!</span>
  </div>
  <h1 class="headline headline--centered" style="top:178px;">How to launch a<br>multi-million business<br>from scratch</h1>
</section>

<!-- photo top, band -->
<section class="tile tile--3">
  <div class="photo" role="img" aria-label="Photo of the two hosts speaking on stage" style="left:0; top:0; width:310px; height:128px; border-radius:0; background:linear-gradient(180deg,#7BADD7,#0677BA);"></div>
  <div class="badge badge--sm" style="left:208px; top:38px;">
    <svg viewBox="0 0 92 84" width="92" height="84"><path d="M10 4 H84 V66 H48 L34 80 V66 H10 Z" fill="none" stroke="#fff" stroke-width="2"/></svg>
    <span>Sign up<br>today!</span>
  </div>
  <div class="band" style="top:128px; height:48px; background:var(--navy); border-top:2px solid var(--sky); border-bottom:2px solid var(--sky);"></div>
  <h2 class="course-name" style="left:0; width:310px; text-align:center; top:140px;">The Harvest Ledger Circle</h2>
  <div class="band" style="top:178px; height:132px; background:var(--mid);"></div>
  <h1 class="headline headline--centered" style="top:188px;">How to launch a<br>multi-million business<br>from scratch</h1>
</section>

<!-- dome -->
<section class="tile tile--4">
  <h2 class="course-name" style="left:0; width:310px; text-align:center; top:13px;">The Harvest Ledger Circle</h2>
  <svg class="band" style="top:150px; height:160px;" viewBox="0 0 310 160" width="310" height="160">
    <path d="M0 160 L0 130 Q0 20 155 20 Q310 20 310 130 L310 160 Z" fill="#0677BA" stroke="#CADEEF" stroke-width="1"/>
  </svg>
  <div class="photo" role="img" aria-label="Photo of the two hosts smiling, arms crossed" style="left:92px; top:46px; width:124px; height:134px;"></div>
  <div class="band" style="left:75px; width:160px; top:180px; height:2px; background:var(--ice);"></div>
  <div class="badge badge--sm" style="left:221px; top:74px;">
    <svg viewBox="0 0 92 84" width="92" height="84"><path d="M10 4 H84 V66 H48 L34 80 V66 H10 Z" fill="none" stroke="#fff" stroke-width="2"/></svg>
    <span>Sign up<br>today!</span>
  </div>
  <h1 class="headline headline--centered" style="top:190px; font-size:34px;">How to launch a<br>multi-million business<br>from scratch</h1>
</section>

<!-- light header, photo bottom -->
<section class="tile tile--5">
  <div class="band" style="top:0; height:54px; background:var(--ice);"></div>
  <h2 class="course-name course-name--dark" style="left:0; width:310px; text-align:center; top:15px;">The Harvest Ledger Circle</h2>
  <h1 class="headline headline--centered" style="top:62px;">How to launch a<br>multi-million business<br>from scratch</h1>
  <svg class="band" style="top:188px; height:122px;" viewBox="0 0 310 122" width="310" height="122">
    <path d="M0 0 L60 40 L250 40 L310 0 L310 122 L0 122 Z" fill="#0677BA"/>
  </svg>
  <div class="photo" role="img" aria-label="Photo of the two course hosts standing together" style="left:52px; top:180px; width:160px; height:130px; border-radius:6px 6px 0 0;"></div>
  <div class="badge badge--sm" style="left:218px; top:196px;">
    <svg viewBox="0 0 92 84" width="92" height="84"><path d="M10 4 H84 V66 H48 L34 80 V66 H10 Z" fill="none" stroke="#fff" stroke-width="2"/></svg>
    <span>Sign up<br>today!</span>
  </div>
</section>

<!-- light header, photo bottom right -->
<section class="tile tile--6">
  <div class="band" style="top:0; height:60px; background:var(--ice);"></div>
  <h2 class="course-name course-name--dark" style="left:0; width:310px; text-align:center; top:18px;">The Harvest Ledger Circle</h2>
  <h1 class="headline headline--centered" style="top:70px;">How to launch a<br>multi-million business<br>from scratch</h1>
  <div class="photo" role="img" aria-label="Photo of the two hosts speaking on stage" style="left:145px; top:185px; width:165px; height:125px; border-radius:6px 0 0 0;"></div>
  <div class="badge badge--sm" style="left:44px; top:204px;">
    <svg viewBox="0 0 92 84" width="92" height="84"><path d="M10 4 H84 V66 H48 L34 80 V66 H10 Z" fill="none" stroke="#fff" stroke-width="2"/></svg>
    <span>Sign up<br>today!</span>
  </div>
</section>

</body>
</html>
```